Candle Rental Business seeks new website design

We need a new website design for a Candle hire business. The business rents out pillar candles for events such as weddings and corporate events. Our main target market is weddings. The business name is Hire a Lantern. The business name does not have a logo design.

We would like a website that is light in colours and creates a warm atmosphere. The design needs to be elegant and upmarket. There are different size candles that we hire out, ranging from 10cm diameter to 20cm diameter, flat, tall etc. All our candles are white in colour. Its just the size that differs.

We would also like to include a section for hiring out decor such as glassvases, candlebras, overlays and chairs sachets, chair covers. However, this is not the businesses main focus but an additional offering to customers.

Target Market(s)

Wedding venues and brides. Corporate events. School dances.

Industry/Entity Type

Hospitality

Logo Text

Hire a Lantern

Number of Pages Required

1 page

Font styles to use
Sans Serif
Script

Requirements
Must have
• Pictures of pillar candles. Plain white candles. The website must centre around candles.
Nice to have
• Different examples of candle centrepieces
Should not have
• Pictures must not be of brides. Pictures of surrounding is perferable.

```html
<!DOCTYPE html>
<html lang="en">
<head>
<meta charset="utf-8">
<title>Hire a Lantern — Candle Hire for Weddings &amp; Events</title>
<link href="https://fonts.googleapis.com/css2?family=Great+Vibes&family=Open+Sans:wght@400;600;700&display=swap" rel="stylesheet">
<style>
:root{
  --pink:#d6237f;
  --pink-deep:#b3166a;
  --pink-soft:#f4c6dc;
  --ink:#3a3a3a;
  --muted:#7d7d7d;
  --light:#f7f4f2;
  --white:#ffffff;
  --footer:#1f1f1f;
  --footer-base:#141414;
  --script:'Great Vibes', cursive;
  --sans:'Open Sans', sans-serif;
}
*{margin:0;padding:0;box-sizing:border-box}
html,body{width:1200px;height:3004px;overflow:hidden}
body{font-family:var(--sans);color:var(--ink);background:var(--white);position:relative}
.script{font-family:var(--script);font-weight:400}

/* top bar */
.topbar{height:28px;background:var(--pink-soft);display:flex;justify-content:flex-end;align-items:center;gap:34px;padding-right:120px;font-size:11px;color:var(--pink-deep)}
.topbar span{display:flex;align-items:center;gap:6px}
.topbar svg{width:12px;height:12px}

/* header */
.header{height:92px;display:flex;align-items:center;justify-content:space-between;padding:0 110px;border-bottom:1px solid #eee}
.brand{display:flex;align-items:center;gap:12px}
.brand-dot{width:34px;height:34px;border-radius:50%;background:var(--pink)}
.brand-name{font-family:var(--script);font-size:36px;color:var(--pink)}
.nav{display:flex;gap:4px;list-style:none}
.nav li{font-size:12px;font-weight:600;text-transform:uppercase;padding:8px 12px;color:var(--ink)}
.nav li.active{color:var(--pink);border-bottom:2px solid var(--pink)}

/* hero */
.hero{position:relative;height:520px}
.hero-photo{position:absolute;inset:0;background:linear-gradient(180deg,#d9d4d0 0%,#ece8e3 45%,#f6f1ea 70%,#c9b07a 100%)}
.hero-card{position:absolute;left:390px;top:370px;width:420px;height:130px;background:var(--white);border:1px solid #ddd;box-shadow:0 4px 14px rgba(0,0,0,.15);text-align:center;padding-top:18px}
.hero-card::before{content:"";position:absolute;inset:8px;border:1px solid var(--pink-soft)}
.hero-card h1{font-family:var(--script);font-weight:400;font-size:46px;color:var(--pink);line-height:1}
.hero-card p{font-family:var(--script);font-size:28px;color:var(--pink-deep);margin-top:8px}

/* candles */
.candles{height:560px;background:var(--light);text-align:center;padding-top:132px}
.section-title{font-family:var(--script);font-weight:400;font-size:56px;color:var(--pink);line-height:1}
.title-rule{width:120px;height:2px;background:var(--pink-soft);margin:10px auto 0}
.candle-row{display:flex;justify-content:center;gap:50px;margin-top:64px}
.candle-item{width:214px;height:214px;border-radius:50%;border:7px solid var(--pink-deep);position:relative;overflow:hidden}
.candle-photo{position:absolute;inset:0;background:radial-gradient(circle at 50% 55%,#f3c16e 0%,#b0521d 45%,#3b1509 100%)}
.candle-item span{position:absolute;left:0;right:0;top:88px;font-family:var(--script);font-size:32px;color:var(--white);text-shadow:0 1px 3px rgba(0,0,0,.6)}

/* welcome */
.welcome{height:500px;position:relative}
.welcome-photo{position:absolute;left:170px;top:110px;width:400px;height:260px;background:radial-gradient(ellipse at 45% 40%,#d8262f 0%,#a51419 35%,#e9ece9 70%,#ffffff 100%)}
.welcome-text{position:absolute;left:640px;top:132px;width:460px}
.welcome-text h2{font-family:var(--script);font-weight:400;font-size:48px;color:var(--ink);line-height:1}
.welcome-text p{font-size:11px;line-height:18px;color:var(--muted);margin-top:16px}
.btn{display:inline-block;margin-top:22px;background:var(--pink-deep);color:var(--white);font-size:11px;font-weight:700;padding:8px 16px;text-transform:uppercase;letter-spacing:.5px}

/* decor */
.decor{height:580px;background:linear-gradient(180deg,var(--pink) 0%,var(--pink-deep) 100%);position:relative;text-align:center;padding-top:50px}
.decor .section-title{color:var(--white)}
.decor .title-rule{background:rgba(255,255,255,.5)}
.decor-row{display:flex;justify-content:center;gap:62px;margin-top:58px}
.decor-card{width:180px;height:350px;background:var(--white);box-shadow:0 4px 10px rgba(0,0,0,.2)}
.decor-photo{height:170px}
.decor-card h3{font-family:var(--script);font-weight:400;font-size:32px;color:var(--ink);margin-top:22px}
.decor-card p{font-size:10px;line-height:16px;color:var(--muted);padding:10px 16px 0}
.arrow{position:absolute;top:290px;width:24px;height:40px}
.arrow.left{left:40px}.arrow.right{right:40px}

/* blog */
.blog{height:400px;text-align:center;padding-top:44px}
.blog .section-title{color:var(--ink)}
.blog-row{display:flex;justify-content:center;gap:40px;margin-top:50px}
.post{display:flex;gap:22px;text-align:left;width:470px}
.post-photo{width:200px;height:160px;flex:none}
.post h4{font-size:13px;font-weight:600;color:var(--ink)}
.post-meta{margin-top:8px;display:flex;gap:6px}
.post-meta span{background:var(--pink);color:var(--white);font-size:9px;font-weight:700;padding:2px 6px}
.post p{font-size:10px;line-height:16px;color:var(--muted);margin-top:10px}

/* footer */
.footer{height:280px;background:var(--footer);color:#cfcfcf;display:flex;padding:40px 100px 0;gap:0}
.footer h5{font-size:12px;font-weight:700;color:var(--white);text-transform:uppercase;margin-bottom:16px}
.footer ul{list-style:none;font-size:11px;line-height:22px}
.footer li{display:flex;align-items:center;gap:8px}
.footer svg{width:13px;height:13px;flex:none}
.col-contact{width:320px}
.col-links{width:260px}
.col-social{width:180px}
.col-news{width:240px}
.social-dot{width:14px;height:14px;border-radius:50%;background:var(--pink);flex:none}
.col-news p{font-size:11px;line-height:17px}
.news-input{margin-top:14px;height:30px;background:var(--white);color:#999;font-size:11px;padding:7px 10px}
.news-btn{margin-top:12px;display:inline-block;background:var(--pink-deep);color:var(--white);font-size:11px;font-weight:700;padding:7px 14px;text-transform:uppercase}
.base{height:44px;background:var(--footer-base);color:#8a8a8a;font-size:10px;text-align:center;line-height:44px}
</style>
</head>
<body>

<div class="topbar">
  <span><svg viewBox="0 0 12 12"><path d="M2 1h3l1 3-1.5 1a7 7 0 0 0 2.5 2.5L8 6l3 1v3c0 .6-.4 1-1 1A9 9 0 0 1 1 2c0-.6.4-1 1-1z" fill="currentColor"/></svg>1-800-555-0147</span>
  <span>Sign In</span>
  <span>Register</span>
</div>

<header class="header">
  <div class="brand"><div class="brand-dot"></div><div class="brand-name">Hire a Lantern</div></div>
  <ul class="nav">
    <li class="active">Home</li><li>About Us</li><li>Products</li><li>Other Services</li><li>Blogs</li><li>Contact Us</li>
  </ul>
</header>

<section class="hero">
  <div class="hero-photo" role="img" aria-label="Wedding table with white roses, glasses and lit pillar candles"></div>
  <div class="hero-card">
    <h1>Hire a Lantern</h1>
    <p>Weddings &amp; Corporate Events</p>
  </div>
</section>

<section class="candles">
  <h2 class="section-title">Our Candles</h2>
  <div class="title-rule"></div>
  <div class="candle-row">
    <div class="candle-item"><div class="candle-photo" role="img" aria-label="Lit white pillar candle, 10cm diameter"></div><span>10cm Diameter</span></div>
    <div class="candle-item"><div class="candle-photo" role="img" aria-label="Lit white pillar candles, 12cm diameter"></div><span>12cm Diameter</span></div>
    <div class="candle-item"><div class="candle-photo" role="img" aria-label="Lit white pillar candles, 15cm diameter"></div><span>15cm Diameter</span></div>
    <div class="candle-item"><div class="candle-photo" role="img" aria-label="Lit white pillar candles, 20cm diameter"></div><span>20cm Diameter</span></div>
  </div>
</section>

<section class="welcome">
  <div class="welcome-photo" role="img" aria-label="Red pillar candles with pine sprigs and ornaments in snow"></div>
  <div class="welcome-text">
    <h2>Welcome To Hire a Lantern</h2>
    <p>We bring soft, warm candlelight to weddings, venues and corporate evenings. Our white pillar candles come in many sizes, from slim and tall to wide and flat, ready to set a calm, elegant mood at every table.</p>
    <p>Tell us about your event and we will plan the right mix of candles and holders. We deliver, set up and collect, so you can enjoy the glow while we take care of every small detail for you.</p>
    <span class="btn">Read More</span>
  </div>
</section>

<section class="decor">
  <h2 class="section-title">Hiring Out Decor</h2>
  <div class="title-rule"></div>
  <svg class="arrow left" viewBox="0 0 24 40"><path d="M18 4 6 20l12 16" fill="none" stroke="#fff" stroke-width="3"/></svg>
  <svg class="arrow right" viewBox="0 0 24 40"><path d="M6 4l12 16L6 36" fill="none" stroke="#fff" stroke-width="3"/></svg>
  <div class="decor-row">
    <div class="decor-card"><div class="decor-photo" role="img" aria-label="Glass vases with flowers on a table" style="background:linear-gradient(160deg,#cfe3c8,#e8a9b8 60%,#f2efe8)"></div><h3>Glassware</h3><p>Clear vases and bowls for centrepieces, made to hold candles and fresh flowers.</p></div>
    <div class="decor-card"><div class="decor-photo" role="img" aria-label="Tall candelabras lit in a dark hall" style="background:linear-gradient(160deg,#5a3a22,#e8c07a 55%,#3a2416)"></div><h3>Candelabras</h3><p>Tall silver and gold stands that lift candlelight high above each guest table.</p></div>
    <div class="decor-card"><div class="decor-photo" role="img" aria-label="Chairs tied with satin sashes" style="background:linear-gradient(160deg,#f1ece0,#d9c58f 60%,#efe8d8)"></div><h3>Chairs Sashes</h3><p>Satin sashes in many shades, tied neatly to match your theme and your flowers.</p></div>
    <div class="decor-card"><div class="decor-photo" role="img" aria-label="Rows of white chair covers outdoors" style="background:linear-gradient(160deg,#cfe0ea,#f6f6f4 55%,#b9cfa8)"></div><h3>Chair Covers</h3><p>Crisp white covers that dress every seat for a clean and graceful finish.</p></div>
  </div>
</section>

<section class="blog">
  <h2 class="section-title">Latest Blog</h2>
  <div class="blog-row">
    <article class="post">
      <div class="post-photo" role="img" aria-label="White flowers and candles on a reception table" style="background:linear-gradient(160deg,#f1eee6,#d9cfae 60%,#a9b48f)"></div>
      <div>
        <h4>Nemo Enim Ipsam Voluptatem</h4>
        <div class="post-meta"><span>CANDLELIGHT</span><span>4 COMMENTS</span></div>
        <p>Simple ideas for lighting a long banquet table with pillar candles of mixed height, placed in small groups for a soft and even glow through the night.</p>
      </div>
    </article>
    <article class="post">
      <div class="post-photo" role="img" aria-label="Decorated reception hall with chandeliers" style="background:linear-gradient(160deg,#d9c9b8,#f2e2d4 55%,#b58b6e)"></div>
      <div>
        <h4>Nemo Enim Ipsam Voluptatem</h4>
        <div class="post-meta"><span>VENUES</span><span>2 COMMENTS</span></div>
        <p>How venues use candles at the entrance, along the aisle and on every table to create one warm look from the first moment to the last dance.</p>
      </div>
    </article>
  </div>
</section>

<footer class="footer">
  <div class="col-contact">
    <h5>Contact Us</h5>
    <ul>
      <li><svg viewBox="0 0 12 12"><path d="M6 1a3.5 3.5 0 0 1 3.5 3.5C9.5 7 6 11 6 11S2.5 7 2.5 4.5A3.5 3.5 0 0 1 6 1z" fill="#d6237f"/></svg>24 Wickmoor Lane, Suite 8,</li>
      <li style="padding-left:21px">Fernvale, NJ 07990</li>
      <li><svg viewBox="0 0 12 12"><path d="M2 1h3l1 3-1.5 1a7 7 0 0 0 2.5 2.5L8 6l3 1v3c0 .6-.4 1-1 1A9 9 0 0 1 1 2c0-.6.4-1 1-1z" fill="#d6237f"/></svg>1-800-555-0147</li>
      <li><svg viewBox="0 0 12 12"><rect x="1" y="2.5" width="10" height="7" fill="none" stroke="#d6237f"/><path d="M1 2.5l5 4 5-4" fill="none" stroke="#d6237f"/></svg>info@hirealantern.example</li>
    </ul>
  </div>
  <div class="col-links">
    <h5>Quick Links</h5>
    <ul><li>Products</li><li>Other Services</li><li>Reviews</li><li>About Us</li><li>FAQ</li></ul>
  </div>
  <div class="col-social">
    <h5>Social</h5>
    <ul><li><span class="social-dot"></span>Friendbook</li><li><span class="social-dot"></span>Chirper</li><li><span class="social-dot"></span>WorkLink</li></ul>
  </div>
  <div class="col-news">
    <h5>Join Our Newsletter</h5>
    <p>Get candle tips, new sizes and seasonal offers sent to your inbox each month.</p>
    <div class="news-input">Email Address</div>
    <span class="news-btn">Subscribe</span>
  </div>
</footer>
<div class="base">Copyright 2016 | All Rights Reserved - Hire a Lantern</div>

</body>
</html>
```